Firm-Asset: Tomorrow - EU-funded management consulting

A website to inform possible customers about my management consulting services for small and medium sized companies. I am using a funding for small and medium companies to do 10 days of workshops and coaching about leadership, further education and employee's health. The Funding is called "Betriebsgut Zukunft" which means something like: Humans are the value of the company. The official logo is attached as a

Target Market(s)

Small and medium sized companies that want to improve their employee's well being and efficiency.

Industry/Entity Type

Management Consulting

Contact Information for Business Card

Malte Quast, Birkenhainweg 14, 10219 Berlin

Logo Text

BetriebsGut Zukunft - Beratung

Font styles to use
Serif
Sans Serif

Requirements
Must have
• a friendly and professional design
Nice to have
• saying somthing about: employees, leadership, further education and employees health are important to us.
Should not have
• should not be too shimmering

```html
<!DOCTYPE html>
<html lang="en">
<head>
<meta charset="utf-8">
<title>BetriebsGut Zukunft – Beratung</title>
<link href="https://fonts.googleapis.com/css2?family=Open+Sans:wght@300;400;600;700&display=swap" rel="stylesheet">
<style>
:root{
  --blue:#0b5f8f;
  --blue-dark:#08415f;
  --blue-deep:#0a3b57;
  --orange:#e38b1f;
  --orange-dark:#c97412;
  --text:#3b3b3b;
  --muted:#8a8a8a;
  --line:#d9dde1;
  --bg:#ffffff;
  --band:#f2f3f4;
}
*{box-sizing:border-box;margin:0;padding:0}
html,body{width:889px;height:1200px;overflow:hidden}
body{font-family:"Open Sans",Arial,sans-serif;color:var(--text);background:var(--bg);position:relative}
.site-header{position:absolute;top:0;left:0;width:889px;height:95px}
.brand{position:absolute;left:34px;top:14px;display:flex;align-items:center;gap:10px}
.brand-mark{width:30px;height:30px;background:var(--blue)}
.brand-name{font-size:26px;font-weight:600;color:var(--blue-dark);letter-spacing:-.3px;line-height:1}
.brand-tag{position:absolute;left:34px;top:56px;background:var(--blue);color:#fff;font-size:8px;letter-spacing:1px;padding:4px 10px;font-weight:600}
.search{position:absolute;right:36px;top:58px;width:180px;height:22px;border:1px solid var(--line);font-size:9px;color:var(--muted);padding:5px 8px}
.main-nav{position:absolute;top:95px;left:0;width:889px;height:36px;background:var(--blue);display:flex;padding-left:28px}
.main-nav a{color:#fff;text-decoration:none;font-size:11px;font-weight:600;line-height:36px;padding:0 24px;letter-spacing:.3px}
.main-nav a.active{background:var(--blue-dark)}
.hero{position:absolute;top:131px;left:0;width:889px;height:340px;background:linear-gradient(100deg,#b9c6cc 0%,#dfe4e3 35%,#c9b7a6 60%,#8f9aa3 100%)}
.hero-caption{position:absolute;left:34px;top:112px;width:312px;height:98px;background:rgba(227,139,31,.9);color:#fff;padding:16px 20px}
.hero-caption p{font-size:15px;font-weight:300}
.hero-caption h2{font-size:22px;font-weight:400;margin-top:2px}
.hero-dots{position:absolute;left:432px;top:320px;display:flex;gap:6px}
.hero-dots span{width:9px;height:9px;border-radius:50%;background:#fff}
.hero-dots span.on{background:var(--blue-dark)}
.about{position:absolute;top:500px;left:0;width:889px;text-align:center}
.about h1{font-size:25px;font-weight:300;color:var(--text)}
.about p{width:780px;margin:10px auto 0;font-size:9px;line-height:14px;color:var(--muted)}
.features{position:absolute;top:600px;left:34px;width:821px;display:flex;gap:20px}
.feature{flex:1;height:190px;border:1px solid var(--line);text-align:center;padding:18px 22px 0;position:relative}
.feature-icon{width:44px;height:44px;border-radius:50%;background:var(--blue-dark);margin:0 auto;display:flex;align-items:center;justify-content:center}
.feature h3{font-size:17px;font-weight:400;color:var(--blue-dark);margin-top:10px}
.feature p{font-size:8.5px;line-height:13px;color:var(--muted);margin-top:6px}
.btn{display:inline-block;background:var(--orange);color:#fff;font-size:8px;font-weight:600;padding:5px 14px;margin-top:12px;letter-spacing:.5px}
.topics{position:absolute;top:840px;left:34px;width:821px;height:152px;display:flex;gap:4px}
.topic{flex:1;display:flex}
.topic-photo{width:50%;height:100%}
.topic-text{width:50%;height:100%;color:#fff;padding:18px 16px}
.topic-text h3{font-size:19px;font-weight:300}
.topic-text p{font-size:8.5px;line-height:13px;margin-top:8px}
.topic.health .topic-photo{background:linear-gradient(135deg,#3d8fc6,#9fc4dc 60%,#e4ecf0)}
.topic.health .topic-text{background:var(--blue)}
.topic.education .topic-photo{background:linear-gradient(135deg,#c9a27a,#e7d4bd 55%,#8b6b52)}
.topic.education .topic-text{background:var(--orange)}
.clients{position:absolute;top:1020px;left:0;width:889px;height:64px;background:var(--band);display:flex;align-items:center;justify-content:space-around;padding:0 50px}
.client{font-size:15px;font-weight:700;color:#a7abae;letter-spacing:.5px}
.site-footer{position:absolute;top:1100px;left:0;width:889px;height:100px;background:var(--blue-deep);color:#fff}
.footer-nav{position:absolute;left:34px;top:30px;font-size:9px;font-weight:600;letter-spacing:.3px}
.footer-nav a{color:#fff;text-decoration:none}
.copyright{position:absolute;left:34px;top:48px;font-size:8px;color:#a9c1cf}
.social{position:absolute;right:36px;top:24px;display:flex;gap:5px}
.social span{width:18px;height:18px;border-radius:50%;background:var(--blue)}
.social span:last-child{background:var(--orange-dark)}
</style>
</head>
<body>
<header class="site-header">
  <div class="brand"><span class="brand-mark"></span><span class="brand-name">BetriebsGut Zukunft</span></div>
  <div class="brand-tag">BETRIEBSGUT ZUKUNFT – BERATUNG</div>
  <div class="search">Search</div>
</header>
<nav class="main-nav">
  <a class="active" href="#">HOME</a><a href="#">ABOUT US</a><a href="#">SERVICES</a><a href="#">CONSULTING</a><a href="#">CLIENTS</a><a href="#">TEAM</a><a href="#">CONTACT</a>
</nav>
<section class="hero" role="img" aria-label="Photo of a team workshop with colleagues around a table">
  <div class="hero-caption"><p>Mauris vel lacus vitae felis</p><h2>Proin nulla arcu nonumm</h2></div>
  <div class="hero-dots"><span class="on"></span><span></span><span></span><span></span></div>
</section>
<section class="about">
  <h1>About Betriebsgut Zukunft</h1>
  <p>Supporting small and medium sized companies in building strong teams through funded workshops and coaching. We focus on leadership, further education and the health of every employee, because people are the true value of a company. Ten days of practical guidance, shaped around your daily work and your goals.</p>
</section>
<section class="features">
  <article class="feature">
    <div class="feature-icon"><svg width="22" height="22" viewBox="0 0 22 22"><text x="11" y="18" text-anchor="middle" font-family="Open Sans, sans-serif" font-size="20" font-weight="700" fill="#fff">?</text></svg></div>
    <h3>What We Do</h3>
    <p>Our consulting helps managers and teams grow together with clear goals, open dialogue and practical tools for everyday work.</p>
    <span class="btn">READ MORE</span>
  </article>
  <article class="feature">
    <div class="feature-icon"><svg width="24" height="22" viewBox="0 0 24 22"><path d="M2 3h20v12H10l-5 4v-4H2z" fill="#fff"/></svg></div>
    <h3>Consulting Service</h3>
    <p>Funded workshops and coaching sessions tailored to small and medium sized companies and the people who carry them forward.</p>
    <span class="btn">READ MORE</span>
  </article>
  <article class="feature">
    <div class="feature-icon"><svg width="22" height="22" viewBox="0 0 22 22"><path d="M11 1l3 6.5 7 .8-5.2 4.8 1.4 7L11 16.6 4.8 20.1l1.4-7L1 8.3l7-.8z" fill="#fff"/></svg></div>
    <h3>Leadership</h3>
    <p>Strong leadership builds trust. We coach executives to lead with clarity, empathy and a steady view of what matters most.</p>
    <span class="btn">READ MORE</span>
  </article>
</section>
<section class="topics">
  <div class="topic health">
    <div class="topic-photo" role="img" aria-label="Photo of relaxed employees outdoors"></div>
    <div class="topic-text"><h3>Employee Health</h3><p>Healthy employees work with more energy and joy. We help you create conditions that keep your team well and motivated.</p></div>
  </div>
  <div class="topic education">
    <div class="topic-photo" role="img" aria-label="Photo of a training session with a presenter"></div>
    <div class="topic-text"><h3>Further Education</h3><p>Learning never stops. Targeted further education opens new skills and perspectives for every member of your staff.</p></div>
  </div>
</section>
<section class="clients">
  <span class="client">KESTREL</span><span class="client">Lumora</span><span class="client">TARNWELL</span><span class="client">veldana</span><span class="client">OAKRIDGE</span><span class="client">BRINDLE</span>
</section>
<footer class="site-footer">
  <div class="footer-nav"><a href="#">HOME</a> | <a href="#">ABOUT US</a> | <a href="#">SERVICES</a> | <a href="#">CONSULTING</a> | <a href="#">CLIENTS</a> | <a href="#">TEAM</a> | <a href="#">CONTACT</a></div>
  <div class="copyright">© 2014 Betriebsgut Zukunft. All rights reserved.</div>
  <div class="social"><span></span><span></span><span></span><span></span></div>
</footer>
</body>
</html>
```